Stationery Design Project for Nimbora, Chicago

Nimbora, a street parking application which helps car drivers find a street parking spot by offering an ideal path along which to look for parking. This path is calculated by our algorithm based on data (e.g. historical data, baseball games schedule, etc.). Along this path the driver will find a spot and will also save 70% of the search time. Customer we target is reg. between 21 and 45 yo.

We envision something young, fresh, bright and original. Slightly abstract maybe. It should represent the idea and elements of finding street parking in the city, e.g. car(s), parking spot, people, city, etc. (just ideas!).

Logo is attached.

Requirement:
- Business Cards (2 Sided Full Color CMYK)
- Letterhead (1 Sided Full Color CMYK)
- Envelope (1 Sided Full Color CMYK)
- Sticker (1 Sided Full Color CMYK), round with a 2inch diameter.

Reason: We're starting to get more and more designs and need more time to look into all of them. Very exciting!! Thanks to everybody!

Hi all, we're in the process of selecting our favs. Though choices!!! Really good submissions. Will keep you posted and sorry for the delay.

Target Market(s)

Car drivers and owners between 21 and 45

Industry/Entity Type

Parking

Requirements
Must have
• Sticker should be round and include company URL nimbora.com and the new logo which we will attach soon.
Should not have
• Should not be too serious or boring.

```html
<!DOCTYPE html>
<html lang="en">
<head>
<meta charset="utf-8">
<title>Nimbora Business Card</title>
<link rel="stylesheet" href="https://fonts.googleapis.com/css2?family=Source+Sans+3:wght@400;600&display=swap">
<style>
  :root {
    --backdrop: #e9e6e1;
    --card-white: #ffffff;
    --ink: #3b3b3d;
    --ink-soft: #333333;
    --accent-blue: #2a9fd6;
    --deep-blue: #1f4fa8;
    --mark-blue: #1c63d6;
    --charcoal: #2f2f31;
    --charcoal-light: #4a4a4c;
    --swoosh-black: #1b1b1c;
    --paper-text: #ffffff;
  }
  * { box-sizing: border-box; margin: 0; padding: 0; }
  html, body {
    width: 1200px; height: 402px; overflow: hidden;
    background: var(--backdrop);
    font-family: "Source Sans 3", "Helvetica Neue", Arial, sans-serif;
  }
  .sheet { position: relative; width: 1200px; height: 402px; }
  .card {
    position: absolute; top: 57px; width: 515px; height: 294px; overflow: hidden;
    box-shadow: 0 2px 6px rgba(0,0,0,0.25);
  }
  .card--front { left: 59px; background: var(--card-white); }
  .card--back {
    left: 634px;
    background: radial-gradient(ellipse at 50% 40%, var(--charcoal-light), var(--charcoal) 75%);
  }
  .brand { position: absolute; left: 48px; top: 30px; display: flex; align-items: center; gap: 14px; }
  .brand__dot { width: 80px; height: 80px; border-radius: 50%; background: var(--mark-blue); }
  .brand__name { font-size: 60px; font-weight: 400; color: var(--ink); letter-spacing: 1px; line-height: 1; }
  .holder { position: absolute; left: 55px; top: 148px; font-size: 19px; color: var(--accent-blue); }
  .holder__name { font-weight: 600; }
  .holder__title { font-size: 16px; }
  .contacts { position: absolute; left: 55px; top: 186px; list-style: none; font-size: 13px; color: var(--ink-soft); }
  .contacts li { display: flex; align-items: center; gap: 7px; height: 18.5px; }
  .contacts svg { width: 10px; height: 10px; fill: var(--ink-soft); }
  .swoosh { position: absolute; left: 0; top: 0; }
  .address {
    position: absolute; right: 17px; top: 254px; text-align: right;
    font-size: 13.5px; line-height: 19px; color: var(--paper-text);
  }
  .back-mark {
    position: absolute; left: 188px; top: 60px; width: 140px; height: 140px;
    border-radius: 50%; background: var(--mark-blue);
  }
  .back-url {
    position: absolute; left: 0; width: 100%; top: 250px; text-align: center;
    font-size: 18px; letter-spacing: 2px; color: var(--paper-text);
  }
</style>
</head>
<body>
<main class="sheet">
  <section class="card card--front" aria-label="Business card front">
    <svg class="swoosh" width="515" height="294" viewBox="0 0 515 294" aria-hidden="true">
      <path d="M0,294 L0,268 C140,300 320,232 515,186 L515,294 Z" fill="var(--charcoal)"/>
      <path d="M0,262 C150,292 330,222 515,170 L515,186 C320,232 140,300 0,268 Z" fill="var(--deep-blue)"/>
      <path d="M0,258 C150,288 330,218 515,166 L515,170 C330,222 150,292 0,262 Z" fill="#ffffff"/>
      <path d="M380,214 C420,190 470,168 515,150 L515,162 C470,178 420,198 380,214 Z" fill="var(--swoosh-black)"/>
      <path d="M0,230 C40,260 100,285 190,292 C110,292 40,275 0,252 Z" fill="var(--swoosh-black)"/>
    </svg>
    <div class="brand">
      <span class="brand__dot"></span>
      <span class="brand__name">Nimbora</span>
    </div>
    <p class="holder"><span class="holder__name">Your Name ,</span> <span class="holder__title">Title</span></p>
    <ul class="contacts">
      <li><svg viewBox="0 0 10 10"><path d="M2,0 L4,2 L3,3.5 Q4.5,6 6.5,7 L8,6 L10,8 L8.5,10 Q2,9 0,1.5 Z"/></svg>+91 98765 43210</li>
      <li><svg viewBox="0 0 10 10"><rect x="2.5" y="0" width="5" height="10" rx="1"/></svg>+91 98765 43210</li>
      <li><svg viewBox="0 0 10 10"><path d="M0,2 H10 V9 H0 Z M0,2 L5,6 L10,2" stroke="#fff" stroke-width="0.8"/></svg>info@nimbora.com</li>
      <li><svg viewBox="0 0 10 10"><circle cx="5" cy="5" r="5"/></svg>www.nimbora.com</li>
    </ul>
    <p class="address">Complex Name, Street Name<br>Area, City Name,000 000</p>
  </section>

  <section class="card card--back" aria-label="Business card back">
    <span class="back-mark"></span>
    <p class="back-url">www.nimbora.com</p>
  </section>
</main>
</body>
</html>
```